Corvane Paintless Dent Removal

Our company works on vehicles removing dents using a highly skilled trade which the metal is massaged out with special tools without disturbing the original paint, hence paintless dent removal. Besides keeping the paint and metal original its also very environmentally friendly since no paint or toxic fillers are used. Also we we are one of the most experienced companies in the business with 25 years

Target Market(s)

Retail Automobile consumers, Auto Dealerships and Auto Body Shops

Industry/Entity Type

Auto Repair

Contact Information for Business Card

Dale Hollister
PO Box 518 Brookmere, NY 11962
631-555-0148
corvanepdr@mailbox-example.com
website corvanepdr.example
youtube corvane paintless dent removal
25 years of experience removing Dents, Dings and Hail Damage

Font styles to use
Serif
Sans Serif

Colors

Designer to choose colors to be used in the design.

Requirements
Must have
• I do like things that are simple but classy and somewhat bold, also I like my logo so that should be somewhat important

```html
<!DOCTYPE html>
<html lang="en">
<head>
<meta charset="utf-8">
<title>Corvane Paintless Dent Removal – Business Card</title>
<link rel="stylesheet" href="https://fonts.googleapis.com/css2?family=Roboto:wght@400;500;700;900&display=swap">
<style>
  :root {
    --navy: #13254a;
    --green: #76bd22;
    --white: #ffffff;
    --paper: #f3f3f3;
    --ink: #1c2433;
    --backdrop: #c8c8c8;
    --video-red: #d9251c;
  }
  * { margin: 0; padding: 0; box-sizing: border-box; }
  html, body { width: 1200px; height: 576px; overflow: hidden; }
  body {
    background: var(--backdrop);
    font-family: "Roboto", Arial, sans-serif;
    position: relative;
  }
  .card {
    position: absolute;
    top: 138px;
    border-radius: 12px;
    overflow: hidden;
    box-shadow: 0 3px 6px rgba(0,0,0,0.25);
  }
  /* Front */
  .card-front {
    left: 82px;
    width: 485px;
    height: 294px;
    background: var(--navy);
  }
  .brand {
    position: absolute;
    left: 0; right: 0;
    text-align: center;
    font-weight: 900;
    line-height: 1;
  }
  .brand-name { display: block; font-size: 44px; letter-spacing: 0.5px; text-transform: uppercase; }
  .brand-tag { display: block; font-size: 15px; margin-top: 4px; }
  .card-front .brand { top: 110px; color: var(--white); }
  .front-footer {
    position: absolute;
    left: 61px; right: 63px;
    top: 262px;
    display: flex;
    align-items: center;
    gap: 18px;
  }
  .front-footer .rule { flex: 1; height: 1.5px; background: var(--green); }
  .front-footer .url { color: #d9dde6; font-size: 13px; letter-spacing: 0.3px; }
  .front-footer .url span { color: var(--green); }

  /* Back */
  .card-back {
    left: 602px;
    width: 481px;
    height: 292px;
    background: var(--paper);
  }
  .back-swoosh { position: absolute; inset: 0; }
  .holder {
    position: absolute;
    right: 25px;
    top: 22px;
    text-align: right;
    color: var(--white);
  }
  .holder-name { font-size: 20px; font-weight: 700; }
  .holder-title { font-size: 11.5px; margin-top: 5px; }
  .card-back .brand { top: 108px; left: 12px; right: auto; width: 300px; color: var(--navy); }
  .card-back .brand-name { font-size: 38px; }
  .card-back .brand-tag { font-size: 13px; }
  .contact-list {
    position: absolute;
    left: 29px;
    top: 219px;
    list-style: none;
    color: var(--ink);
    font-size: 12.5px;
  }
  .contact-list li { display: flex; align-items: center; height: 16.5px; }
  .contact-list svg { width: 11px; height: 11px; margin-right: 9px; fill: var(--green); }
  .contact-right {
    position: absolute;
    right: 25px;
    top: 235px;
    text-align: right;
    color: var(--ink);
    font-size: 12.5px;
    line-height: 19px;
  }
  .video-channel { display: flex; align-items: center; justify-content: flex-end; }
  .video-channel .dot { width: 14px; height: 10px; background: var(--video-red); border-radius: 2px; margin-right: 4px; }
</style>
</head>
<body>

<section class="card card-front">
  <div class="brand">
    <span class="brand-name">Corvane</span>
    <span class="brand-tag">Paintless Dent Removal</span>
  </div>
  <div class="front-footer">
    <span class="rule"></span>
    <span class="url">www.<span>corvanepdr</span>.example</span>
    <span class="rule"></span>
  </div>
</section>

<section class="card card-back">
  <svg class="back-swoosh" viewBox="0 0 481 292" preserveAspectRatio="none" aria-hidden="true">
    <path fill="var(--navy)" d="M0 0 H481 V108 C400 106 340 62 260 36 C180 12 80 14 0 36 Z"/>
    <path fill="var(--green)" d="M0 45 C80 22 180 22 255 50 C330 80 390 112 481 113 V122 C390 122 325 96 252 62 C180 32 90 32 0 52 Z"/>
    <path fill="var(--green)" d="M20 42 C90 16 170 12 250 26 C175 20 95 24 20 42 Z"/>
  </svg>

  <div class="holder">
    <div class="holder-name">Dale Hollister</div>
    <div class="holder-title">Managing Director</div>
  </div>

  <div class="brand">
    <span class="brand-name">Corvane</span>
    <span class="brand-tag">Paintless Dent Removal</span>
  </div>

  <ul class="contact-list">
    <li>
      <svg viewBox="0 0 24 24"><path d="M6.6 10.8a15.1 15.1 0 0 0 6.6 6.6l2.2-2.2c.3-.3.7-.4 1-.2 1.1.4 2.3.6 3.6.6.6 0 1 .4 1 1V20c0 .6-.4 1-1 1A17 17 0 0 1 3 4c0-.6.4-1 1-1h3.5c.6 0 1 .4 1 1 0 1.3.2 2.5.6 3.6.1.3 0 .7-.2 1z"/></svg>
      631-555-0148
    </li>
    <li>
      <svg viewBox="0 0 24 24"><path d="M2 5h20v14H2z M3 6l9 7 9-7" fill="var(--green)"/><path d="M3 6.5l9 6.5 9-6.5" fill="none" stroke="#fff" stroke-width="1.6"/></svg>
      corvanepdr@mailbox-example.com
    </li>
    <li>
      <svg viewBox="0 0 24 24"><circle cx="12" cy="12" r="10"/><path d="M2 12h20M12 2c3 3 3 17 0 20M12 2c-3 3-3 17 0 20" fill="none" stroke="#fff" stroke-width="1.4"/></svg>
      www.corvanepdr.example
    </li>
  </ul>

  <div class="contact-right">
    <div class="video-channel"><span class="dot"></span>/Dale Hollister</div>
    <div class="address">PO Box 518 Brookmere, NY 11962</div>
  </div>
</section>

</body>
</html>
```